Podiatry clinic requires a modern revamp and editing of existing website.

I would like a fresh new look and updated information for my current business website. An easy to navigate site with prominent address and phone number for call to action. We are a podiatry clinic that focuses on general and sports podiatry.
I would like 4 pages; including Home page, About Us, Services & Contact.
www.brambleridgepodiatry.net

Target Market(s)

Active working professionals.

Industry/Entity Type

Medical

Coding

Coded - Design and coding required

Number of Pages Required

4 page

Font styles to use
Sans Serif

Colors
6b449b

Requirements
Must have
• A modern look with logo and active images; clean and uncluttered. Visible phone number and address for call to action.
• 4 pages - Home, About Us, Services, Contact.
• Home page - update address & service logos.
• About Us - update of personal information.
• Services - Revamp of existing page.
• Contact page to include Google map, email & phone number.
Nice to have
• Ability to add content easily; eg. a blog or adding video onto Home page.
• Link to Facebook page.

```html
<!DOCTYPE html>
<html lang="en">
<head>
<meta charset="utf-8">
<title>Bramble Ridge Podiatry – Services</title>
<link rel="stylesheet" href="https://fonts.googleapis.com/css2?family=Raleway:wght@300;400;500&family=Open+Sans:wght@400;600&family=Roboto+Condensed:wght@300;400&display=swap">
<style>
:root{
  --purple:#6b449b;
  --purple-dark:#4a2c8c;
  --purple-light:#c9b8e4;
  --green:#8cc63f;
  --text:#555;
  --heading:#444;
  --rule:#6b5aa8;
  --grey-band:#e8e8e8;
  --white:#fff;
  --footer:#5a3b9a;
}
*{box-sizing:border-box;margin:0;padding:0}
html,body{width:1200px;height:3766px;overflow:hidden}
body{position:relative;background:var(--white);font-family:"Open Sans",sans-serif;color:var(--text)}

/* header */
.site-header{position:absolute;left:0;top:0;width:1200px;height:176px;
  background:linear-gradient(180deg,var(--purple) 0%,#8f6fc0 55%,#ddd2ee 100%)}
.brand{position:absolute;left:75px;top:30px;display:flex;align-items:center;gap:16px}
.brand-dot{width:56px;height:56px;border-radius:50%;background:var(--white)}
.brand-name{font-family:"Raleway",sans-serif;font-weight:500;font-size:34px;line-height:1.05;color:var(--white);width:230px}
.header-contact{position:absolute;right:83px;top:38px;text-align:right;font-family:"Roboto Condensed",sans-serif;color:var(--white)}
.header-contact p{display:flex;align-items:center;justify-content:flex-end;gap:10px;font-size:24px;font-weight:300}
.header-contact p+p{margin-top:20px}
.header-contact strong{font-weight:400}

.main-nav{position:absolute;left:0;top:176px;width:1200px;height:62px;background:var(--purple-dark);display:flex;padding-left:83px}
.main-nav a{display:block;height:62px;line-height:62px;padding:0 34px;color:var(--white);text-decoration:none;font-family:"Raleway",sans-serif;font-size:20px}
.main-nav a.active{background:var(--green)}

/* services intro */
.hero-photo{position:absolute;left:0;top:238px;width:150px;height:252px;
  background:radial-gradient(circle at 40% 60%,#e38a7e 0%,#f2d3c7 45%,#fff 80%)}
.page-title{position:absolute;left:0;top:290px;width:1200px;text-align:center;font-family:"Raleway",sans-serif;font-weight:300;font-size:44px;color:#555}
.page-title span,.section-title span{color:var(--purple-dark)}
.intro{position:absolute;left:210px;top:352px;width:780px;text-align:center;font-size:15px;line-height:25px}

.section-title{text-align:center;font-family:"Raleway",sans-serif;font-weight:400;font-size:34px;color:#555}
.general .section-title{position:absolute;left:0;top:455px;width:1200px}

.treatment-list{position:absolute;left:75px;width:1047px;list-style:none}
.general .treatment-list{top:505px}
.treatment{display:flex;gap:30px;border-bottom:1px solid var(--rule);padding-top:18px}
.general .treatment{height:175px}
.treatment:last-child{border-bottom:none}
.thumb{flex:0 0 135px;height:135px;border-radius:50%}
.treatment h3{font-family:"Raleway",sans-serif;font-weight:400;font-size:22px;color:var(--purple-dark);margin:14px 0 10px}
.treatment p{font-size:15px;line-height:25px}

.tone-a{background:radial-gradient(circle,#f0d4cb,#d9a79a)}
.tone-b{background:radial-gradient(circle,#c9a58a,#3b2a26)}
.tone-c{background:radial-gradient(circle,#e6e2e0,#6d8ea6)}
.tone-d{background:radial-gradient(circle,#f1d9cf,#8a6060)}
.tone-e{background:radial-gradient(circle,#e8c6cf,#4b6f8c)}
.tone-f{background:radial-gradient(circle,#f4e1d8,#d3a492)}
.tone-g{background:radial-gradient(circle,#f7f7f7,#c7c7c7)}
.tone-h{background:radial-gradient(circle,#a48268,#2e3b55)}

/* specialised */
.specialised{position:absolute;left:0;top:1953px;width:1200px;height:959px;background:var(--grey-band)}
.specialised-photo{position:absolute;right:0;top:-25px;width:300px;height:140px;border-radius:70px 0 0 70px;
  background:linear-gradient(90deg,rgba(240,200,185,0) 0%,#efc6b4 40%,#e7b19c 100%)}
.specialised .section-title{position:absolute;left:0;top:45px;width:1200px}
.specialised .treatment-list{top:102px}
.specialised .treatment{height:175px;padding-top:16px}
.specialised .thumb{flex-basis:132px;height:132px}

/* affiliations */
.affiliations{position:absolute;left:0;top:2912px;width:1200px;height:246px;display:flex;align-items:center;justify-content:space-between;padding:0 50px 0 75px}
.badge{height:80px;border-radius:8px}
.badge-1{width:225px;background:#e3e8f2}
.badge-2{width:215px;background:#dbe3f0}
.badge-3{width:220px;background:#e4f0d6}
.badge-4{width:245px;background:#ececec}

/* contact */
.contact{position:absolute;left:0;top:3158px;width:1200px;height:552px;
  background:linear-gradient(180deg,#3e3834 0%,#5a4f45 45%,#2d2a28 100%)}
.contact-scene{position:absolute;right:120px;top:40px;width:200px;height:512px;border-radius:100px 100px 0 0;
  background:linear-gradient(180deg,rgba(70,90,140,.0),rgba(60,80,130,.45))}
.contact h2{position:absolute;left:0;top:45px;width:1200px;text-align:center;font-family:"Raleway",sans-serif;font-weight:300;font-size:46px;color:var(--white)}
.contact-form{position:absolute;left:75px;top:162px;width:440px}
.field{display:block;width:440px;height:52px;background:var(--white);border:none;border-radius:4px;margin-bottom:6px;padding:0 16px;font-family:"Open Sans",sans-serif;font-size:14px;line-height:52px;color:#999}
.field.message{height:104px;line-height:22px;padding-top:14px}
.submit{display:block;margin-top:14px;width:170px;height:50px;border-radius:25px;border:none;background:var(--purple);color:var(--white);font-family:"Raleway",sans-serif;font-size:22px}
.map{position:absolute;left:535px;top:162px;width:273px;height:272px;background:linear-gradient(135deg,#ecebe6,#dcdad3)}
.contact-details{position:absolute;left:853px;top:162px;width:290px;color:var(--white)}
.contact-details h4{font-family:"Raleway",sans-serif;font-weight:400;font-size:20px;margin-bottom:22px}
.contact-details p{display:flex;gap:14px;font-size:15px;line-height:23px;margin-bottom:20px}
.contact-details p svg{flex:0 0 22px;margin-top:2px}
.contact-details strong{font-weight:600}
.social-dot{width:46px;height:46px;border-radius:50%;background:var(--white)}

.site-footer{position:absolute;left:0;top:3710px;width:1200px;height:56px;background:var(--footer);color:var(--white);text-align:center;font-size:14px;line-height:56px}
</style>
</head>
<body>

<header class="site-header">
  <div class="brand">
    <span class="brand-dot"></span>
    <span class="brand-name">Bramble Ridge Podiatry</span>
  </div>
  <div class="header-contact">
    <p><svg width="18" height="24" viewBox="0 0 18 24"><path d="M9 0a9 9 0 0 0-9 9c0 6.5 9 15 9 15s9-8.5 9-15a9 9 0 0 0-9-9zm0 12.5A3.5 3.5 0 1 1 9 5.5a3.5 3.5 0 0 1 0 7z" fill="#fff"/></svg>Suite 12 / 85 Harlow Street Eastbrook 3141</p>
    <p><svg width="26" height="26" viewBox="0 0 24 24"><path d="M6.6 10.8a15.1 15.1 0 0 0 6.6 6.6l2.2-2.2c.3-.3.7-.4 1-.2 1.1.4 2.3.6 3.6.6.6 0 1 .4 1 1V20c0 .6-.4 1-1 1A17 17 0 0 1 3 4c0-.6.4-1 1-1h3.5c.6 0 1 .4 1 1 0 1.3.2 2.5.6 3.6.1.3 0 .7-.2 1z" fill="#fff"/></svg>CALL US NOW : <strong>1300 555 208</strong></p>
  </div>
</header>

<nav class="main-nav">
  <a class="active" href="#">HOME</a>
  <a href="#">ABOUT</a>
  <a href="#">SERVICES</a>
  <a href="#">CONTACT</a>
</nav>

<section class="general">
  <div class="hero-photo" role="img" aria-label="Photo of a person holding a sore foot"></div>
  <h1 class="page-title">SERVICES <span>WE PROVIDE</span></h1>
  <p class="intro">Podiatrists are trained to diagnose and treat all medical conditions that affect the feet and lower limb. At Bramble Ridge Podiatry we provide treatment for general &amp; Sports Podiatry conditions and various specialised treatments:</p>
  <h2 class="section-title">General <span>Treatments</span></h2>
  <ul class="treatment-list">
    <li class="treatment"><div class="thumb tone-a" role="img" aria-label="Photo of nail care"></div><div><h3>Nails</h3><p>Nails for difficult to reach feet; ingrown nails; overly thick nails; fungal nails; nails subjected to trauma.</p></div></li>
    <li class="treatment"><div class="thumb tone-b" role="img" aria-label="Photo of feet with corns"></div><div><h3>Corns</h3><p>Corns - hard dry skin lesions due to concerntrated pressure from footwear or abnormal foot structure.</p></div></li>
    <li class="treatment"><div class="thumb tone-c" role="img" aria-label="Photo of callus treatment"></div><div><h3>Callus</h3><p>Callus - areas of dry skin due to pressure of friction, especially around the heels or bony parts of the feet.</p></div></li>
    <li class="treatment"><div class="thumb tone-d" role="img" aria-label="Photo of a foot being examined for warts"></div><div><h3>Warts</h3><p>Warts - also called Papillomas or Verrucare are a viral infection that causes a lesion on the feet. Warts are commonly contracted from public swimming pools and wet tiled surfaces.</p></div></li>
    <li class="treatment"><div class="thumb tone-e" role="img" aria-label="Photo of skin on the feet"></div><div><h3>Skin Disorders</h3><p>Skin Disorders - fungal infections/ tinea/athlete's foot; dermatitis, sweating feet; foot odour; dry cracked skin.</p></div></li>
    <li class="treatment"><div class="thumb tone-f" role="img" aria-label="Photo of a painful heel"></div><div><h3>Heel pain / Heel Spurs / &nbsp;Arch pain</h3><p>Heel pain / Heel Spurs / &nbsp;Arch pain - Plantar Fasciitis - Common condition that causes pain around the heel or arch area that is caused by factors such as faulty foot biomechanics, poor footwear, sports or work activities, injuries and obesity.</p></div></li>
    <li class="treatment"><div class="thumb tone-g" role="img" aria-label="Illustration of an ankle and lower leg"></div><div><h3>Ankle pain / Shin splints / Knee pain</h3><p>Ankle pain / Shin splints / Knee pain - faulty foot biomechanics or injuries can cause excessive strain and damage to soft tissues like muscles &amp; tendons or bones &amp; joints./ These can be treated with various physical therapies and orthoses/arch supports.</p></div></li>
    <li class="treatment"><div class="thumb tone-h" role="img" aria-label="Photo of a foot with a bunion"></div><div><h3>Bunions / Hammertoes / Toe deformities</h3><p>Bunions / Hammertoes / Toe deformities - Bony joint deformities can be caused by faluty foot biomechanics and conditions such as Arthritis, Diabetes or Gout. We can help manage pain and prevent these conditions from getting worse with various products that supply padding or support, as well as provide advice on appropriate footwear.</p></div></li>
  </ul>
</section>

<section class="specialised">
  <div class="specialised-photo" role="img" aria-label="Photo of hands massaging a foot"></div>
  <h2 class="section-title">Specialised <span>Treatments</span></h2>
  <ul class="treatment-list">
    <li class="treatment"><div class="thumb tone-f" role="img" aria-label="Photo of a diabetic foot check"></div><div><h3>Diabetic Management</h3><p>Diabetic Management - &nbsp;Assessment of blood supply / circulation with Doppler Ultrasound; assessment of nerve sensation via Vibration Perception and Monofilament Pressure testing. management and prevention of wounds or ulcers. General foot care and footwear advice for diabetic feet.</p></div></li>
    <li class="treatment"><div class="thumb tone-a" role="img" aria-label="Photo of nail surgery"></div><div><h3>Nail Surgery</h3><p>Nail Surgery - Minor surgical procedure for the permanent removal of ingrown toenails under local anaesthesia.</p></div></li>
    <li class="treatment"><div class="thumb tone-d" role="img" aria-label="Photo of a biomechanical foot assessment"></div><div><h3>Biomechanical Assessment</h3><p>Biomechanical Assessment - &nbsp;We are able to help diagnose abnormal foot biomechanics that may be contributing to pain, injury or deformities in the foot and lower limb.</p></div></li>
    <li class="treatment"><div class="thumb tone-h" role="img" aria-label="Photo of runners' legs"></div><div><h3>Gait Analysis</h3><p>Gait Analysis - Treadmill video analysis of the gait whilst walking or running to ascertain biomechanical problems or abnormalities of movement that may lead to injury or prevent optimal physical performance.</p></div></li>
    <li class="treatment"><div class="thumb tone-f" role="img" aria-label="Photo of an orthotic insole"></div><div><h3>Orthotic Therapy</h3><p>Orthotic Therapy - Orthose, or arch supports, are designed to control the function of the foot when there is evidence of faulty biomechanics, such as overlay flat or high arched feet or the need to relieve areasor pressure. These may be prefabricated over the counter insoles or custom-made devices.Your podiatrists will assess your foot function and advise which type of device is appropriate for your condition.</p></div></li>
  </ul>
</section>

<section class="affiliations" aria-label="Professional affiliations">
  <div class="badge badge-1"></div>
  <div class="badge badge-2"></div>
  <div class="badge badge-3"></div>
  <div class="badge badge-4"></div>
</section>

<section class="contact">
  <div class="contact-scene" role="img" aria-label="Photo of a runner on a country road"></div>
  <h2>CONTACT US</h2>
  <form class="contact-form">
    <div class="field">Name</div>
    <div class="field">E-Mail</div>
    <div class="field">Phone</div>
    <div class="field message">Message</div>
    <button class="submit" type="button">SUBMIT</button>
  </form>
  <div class="map" role="img" aria-label="Map showing the clinic location"></div>
  <div class="contact-details">
    <h4>CONTACT ADDRESS</h4>
    <p><svg width="22" height="26" viewBox="0 0 18 24"><path d="M9 1a8 8 0 0 0-8 8c0 6 8 14 8 14s8-8 8-14a8 8 0 0 0-8-8zm0 11a3 3 0 1 1 0-6 3 3 0 0 1 0 6z" fill="none" stroke="#fff" stroke-width="1.5"/></svg><span>Suite 12 / 85 Harlow Street<br>Eastbrook 3141.</span></p>
    <p><svg width="22" height="22" viewBox="0 0 24 24"><path d="M6.6 10.8a15.1 15.1 0 0 0 6.6 6.6l2.2-2.2c.3-.3.7-.4 1-.2 1.1.4 2.3.6 3.6.6.6 0 1 .4 1 1V20c0 .6-.4 1-1 1A17 17 0 0 1 3 4c0-.6.4-1 1-1h3.5c.6 0 1 .4 1 1 0 1.3.2 2.5.6 3.6.1.3 0 .7-.2 1z" fill="#fff"/></svg><strong>1300 555 208</strong></p>
    <p><svg width="22" height="18" viewBox="0 0 22 18"><rect x="1" y="1" width="20" height="16" rx="2" fill="none" stroke="#fff" stroke-width="1.5"/><path d="M1 2l10 8 10-8" fill="none" stroke="#fff" stroke-width="1.5"/></svg>info@brambleridgepodiatry.net</p>
    <div class="social-dot" aria-label="Social page link"></div>
  </div>
</section>

<footer class="site-footer">© Bramble Ridge Podiatry- 2016. All Rights Reserved.</footer>

</body>
</html>
```